Web Design Project for Professional/Social Media Networking website

www.SteeringSpectrum.com.au

I am launching a professional/social media networking website called SteeringSpectrum which raises awareness of Diversity topics that impact professional, education and social communities. The Diversity initiative targets gender, age, disability, sexual orientation, race and ethnicity.

I expect the majority of customers will be professional women aged 18-65 across all industries. This brand is designed to empower, support and promote those people under represented across the specified diversity groups. It will appeal to those looking to improve both their professional & personal lives. This will be a platform or organisations to promote themselves on the website, therefore, this must be a high quality professional looking site.

I am looking for a website that is professional, positive and has impact. This project is for the design and coding of the website. I have an idea what I want to see but also open to creative design on presentation of items, various pages and flow.

The coding will consist of making the design function (not just pretty pictures). We would be looking to have the winner work with us on a going forward basis for website design changes, tweaks or modifications (paid of course). Please be honest with regards to programming/coding experience and skills as the functionality/ease of this website is essential to its success.

Key Objectives
•Build brand awareness and assist in providing synergy with all key marketing strategies.
•Create a fresh and compelling website design reflecting what the business stands for it will also be user-friendly, build the company’s corporate image and appeal to defined target markets.
•Generate search engine compatibility by optimizing the site for all the major search engines.
•Integrate a custom Content Management System (CMS) to ensure all updates can be made with ease, improving operational efficiency and reducing time to market with critical information.
•Social media implantation, to create social awareness and increase repeat visitors to the site

Customers:
*Australian market initially then branching out Internationally

Must Have:
Company logo-Attached

Inspiration
This website will have a bit of a TalentHub style functionality. http://www.workwrens.com.au is another good example of the type of functionality I’m looking for. I understand that the functionality will need to be adapted and increased overtime; however, I am looking for the following minimal features:

Option 1l Word press CMS Design l (Eg: workwrens.com.au)

Complete Custom Design
User Friendly Navigation Strategy
Information capture forms (Contact Us)
Rotating banner of images on the home page
CMS - Content Management System to make edits and changes
Membership Area
Blog Integration
Calender & Events Integration
Social Media Plugins
Gallery By Category
Custom URL Structures
Multi-level Navigation
Unlimited Pages Via CMS
iPhone & IPad Compatibility

Option 2 l Custom CMS Design

Complete Custom Design
Membership Area
Directory Listing
Calender Integration for Upcoming Events
Search Functionality ( Tagging System : Individual Profile & business )
Basic SEO Integration
Orbix Metrics
Blog Integration
Forum Integration
Search Engine Submission
Social Media Basic Integration, Friendlane, Chirpex etc.
Custom URL Structures
Multi-level Navigation
Unlimited Pages Via CMS

Option 2 would be my preference, however, guidance on the length of time, cost etc would be welcome. I am happy to increase the budget if required as I appreciate there will be more work involved.

I am looking for the home page to be something different with more of a wow factor and something different to the standard page link menu across the top of the screen.

For the home page I am looking for something a little more striking with a visual impact.

Overall
* Not looking for a cookie cutter template
* Home page simplistic and smooth that shows our "brand"
* Modern browser compatible, CSS, Tablet friendly
* FAST Loading, mouseover buttons, custom icons where necessary

Pages Requested in Design (style, fonts, icons, images, etc flow from page to page).
Home Page
Search Results/directory
Members area/profiles of members
About us
Contact Us
News/features
Updates

Industry/Entity Type

Education

Requirements
Must have
• Logo must be at the Top of each webpage

```html
<!DOCTYPE html>
<html lang="en">
<head>
<meta charset="utf-8">
<title>SteeringSpectrum — Home</title>
<link rel="stylesheet" href="https://fonts.googleapis.com/css2?family=Oswald:wght@400;500&family=PT+Sans:wght@400;700&display=swap">
<style>
:root{
  --blue:#1d5ea8;
  --blue-dark:#134b8c;
  --title-blue:#144f97;
  --orange:#e2782e;
  --ink:#3a3a3a;
  --ink-dark:#2f2f2f;
  --text:#555;
  --rule:#9a9a9a;
  --page:#ececec;
  --panel:#f3f3f3;
  --link:#2a5a9c;
}
*{box-sizing:border-box;margin:0;padding:0}
html,body{width:920px;height:1200px;overflow:hidden}
body{background:var(--page);font-family:"PT Sans",Arial,sans-serif;color:var(--text);position:relative}
.topband{position:absolute;left:0;top:0;width:920px;height:6px;background:var(--blue)}
.sheet{position:absolute;left:69px;top:6px;width:781px;height:1180px;background:#fff}
.abs{position:absolute}

/* header */
.brand{left:78px;top:22px;width:210px;text-align:center}
.brand-mark{width:58px;height:58px;margin:0 auto 10px;background:var(--blue);border-radius:8px}
.brand-name{font-family:"PT Sans",sans-serif;font-size:21px;color:var(--blue-dark);letter-spacing:.5px;white-space:nowrap}
.social{top:32px;width:19px;height:19px;border-radius:3px}
.social.s1{left:643px;background:#5bb7e0}
.social.s2{left:672px;background:#3b5998}
.social.s3{left:702px;background:#ef7b25}
.counter{top:33px;height:16px;border:1px solid #ccc;background:#fafafa;font-size:9px;color:#555;display:flex;align-items:center}
.counter .btn{height:100%;padding:0 4px;display:flex;align-items:center;color:#fff;font-weight:700}
.counter .num{padding:0 5px}
.search{left:642px;top:75px;width:200px;height:21px;border:1px solid #c9c9c9;background:#fff}
.search span{position:absolute;left:13px;top:3px;font-size:10px;color:#aaa;font-style:italic}
.search .go{position:absolute;right:-1px;top:-1px;width:26px;height:21px;background:var(--blue-dark)}

/* nav */
.nav{left:71px;top:123px;height:42px;display:flex}
.nav a{height:42px;display:flex;align-items:center;justify-content:center;font-family:"Oswald",sans-serif;font-weight:500;font-size:14.5px;color:#fff;text-decoration:none;background:linear-gradient(#2468b5,#174f92);border-right:1px solid #3a78c0;letter-spacing:-.2px}
.nav a.current{background:linear-gradient(#4a4a4a,#2e2e2e)}
.nav a.accent{background:linear-gradient(#ee8a3c,#d96c22);border-right:1px solid #f0a060}
.subnav{left:78px;top:166px;width:764px;height:36px;background:#ededed;display:flex;align-items:center}
.subnav span{position:absolute;font-size:11px;color:#333}
.subnav span::before{content:"";display:inline-block;width:3px;height:3px;background:#333;border-radius:50%;margin-right:7px;vertical-align:middle}

/* slider */
.slider{left:77px;top:212px;width:579px;height:194px;border:3px solid var(--blue);background:linear-gradient(90deg,#f07160 0%,#e8493c 45%,#d24a3a 80%,#f06b5a 100%)}
.slide-photo{position:absolute;inset:0}
.caption{position:absolute;left:2px;top:10px;width:181px;height:166px;background:#2c2c2c;border:2px solid #111;padding:14px 14px 0 15px}
.caption h2{font-family:"Oswald",sans-serif;font-weight:400;font-size:15px;line-height:20px;color:#fff;padding-bottom:6px;border-bottom:1px solid #666}
.caption p{font-size:9px;line-height:14.4px;color:#ddd;padding:6px 0 5px;border-bottom:1px solid #666}
.caption a{display:block;margin-top:8px;font-size:9px;color:#8fb2e8}
.prev{position:absolute;left:183px;top:69px;width:29px;height:46px;background:#2c2c2c}
.prev svg{position:absolute;left:9px;top:16px}

/* sidebar contact */
.contact{left:660px;top:212px;width:182px;height:194px;background:linear-gradient(#4e4e4e,#333);border:2px solid #555}
.contact h3{height:40px;display:flex;align-items:center;padding-left:34px;font-family:"Oswald",sans-serif;font-weight:400;font-size:16px;color:#fff;background:linear-gradient(#666,#4a4a4a);position:relative}
.contact h3::before{content:"";position:absolute;left:12px;top:13px;width:15px;height:11px;background:#f2cf6a;border-radius:2px}
.field{position:absolute;left:8px;width:164px;height:21px;background:#f8f8f8;border:1px solid #ccc;font-size:9px;color:#777;padding:5px 9px}
.submit{position:absolute;height:22px;font-family:"Oswald",sans-serif;font-size:12px;display:flex;align-items:center;justify-content:center}
.submit.light{background:linear-gradient(#dfe8f4,#b7c8de);color:#333;border:1px solid #fff}
.submit.dark{background:linear-gradient(#555,#333);color:#fff}

/* panels */
.panel{left:77px;width:573px;background:#fff;border:4px solid var(--panel)}
.panel h2{position:absolute;left:15px;font-family:"Oswald",sans-serif;font-weight:500;font-size:16px;color:var(--title-blue);letter-spacing:-.2px}
.cards{position:absolute;left:15px;display:grid;grid-template-columns:repeat(3,162px);column-gap:23px}
.thumb{height:82px;border:1px solid #ccc;padding:3px}
.thumb div{width:100%;height:100%}
.card h4{font-family:"Oswald",sans-serif;font-weight:400;font-size:14.5px;line-height:21px;color:#333;margin-top:14px;padding-bottom:5px;border-bottom:1px solid var(--rule)}
.card p{font-size:9px;line-height:14.4px;color:#666;text-align:justify;margin-top:6px}
.card .more{margin-top:7px;height:25px;background:#3a3a3a;color:#fff;font-size:9.5px;display:flex;align-items:center;justify-content:flex-end;padding-right:10px}
.card .when{font-size:9px;color:var(--link);padding:5px 0 6px;border-bottom:1px solid var(--rule)}

/* poll */
.poll{left:660px;top:419px;width:182px;height:230px;background:linear-gradient(#3f86cc,#1c5aa3)}
.poll h3{height:38px;display:flex;align-items:center;padding-left:10px;font-family:"Oswald",sans-serif;font-weight:500;font-size:15.5px;color:#fff;background:linear-gradient(#4f92d4,#3a7cc2);border-bottom:1px solid #2a69b0}
.poll .q{position:absolute;left:13px;top:50px;width:160px;font-size:9.5px;line-height:16px;color:#fff;text-align:justify}
.poll ul{position:absolute;left:16px;top:94px;list-style:none}
.poll li{height:24px;font-size:12px;color:#fff;display:flex;align-items:center}
.poll li::before{content:"";width:7px;height:7px;border-radius:50%;background:#e8eef5;margin-right:11px}
.poll .submit{left:18px;top:195px;width:62px;background:#fff;color:#333}

.ad{left:660px;top:654px;width:182px;height:162px;background:linear-gradient(160deg,#f7a231,#ee8f1e)}

.news{left:660px;top:826px;width:182px;height:96px;background:var(--panel)}
.news h3{position:absolute;left:9px;top:10px;font-family:"Oswald",sans-serif;font-weight:500;font-size:15px;color:var(--title-blue)}

.tags{left:669px;top:954px;width:168px;line-height:13px;color:#3c62a8}
.tags span{white-space:nowrap}
.tags .s{font-size:5px;color:#9fb0cf}

.partners-title{left:96px;top:958px;font-family:"Oswald",sans-serif;font-size:13px;color:#555}
.badge{background:#d8d8d8;border-radius:4px}

/* footer */
.footer{left:70px;top:1094px;width:778px;height:92px;background:#474747}
.footer .mark{position:absolute;left:54px;top:16px;width:38px;height:38px;background:#8a8a8a;border-radius:6px}
.footer .name{position:absolute;left:8px;top:59px;font-size:15px;color:#9a9a9a;letter-spacing:.3px}
.footer .row{position:absolute;right:6px;font-size:10px;color:#ddd;display:flex;gap:0}
.footer .row span+span::before{content:"|";margin:0 6px;color:#bbb}
.footer .row.plain span+span::before{content:"";margin:0 5px}
</style>
</head>
<body>
<div class="topband"></div>
<div class="sheet"></div>

<header>
  <div class="abs brand">
    <div class="brand-mark"></div>
    <div class="brand-name">SteeringSpectrum</div>
  </div>
  <div class="abs social s1" title="Chirpex"></div>
  <div class="abs social s2" title="Friendlane"></div>
  <div class="abs social s3" title="Feed"></div>
  <div class="abs counter" style="left:734px"><span class="btn" style="background:#3b5998">Like</span><span class="num">6</span></div>
  <div class="abs counter" style="left:800px"><span class="btn" style="background:#2f7de0">+1</span><span class="num">3</span></div>
  <div class="abs search"><span>Search</span><div class="go">
    <svg width="26" height="21" viewBox="0 0 26 21"><circle cx="12" cy="9" r="4" fill="none" stroke="#fff" stroke-width="1.6"/><line x1="15" y1="12" x2="18" y2="15" stroke="#fff" stroke-width="2"/></svg>
  </div></div>
</header>

<nav class="abs nav">
  <a class="current" style="width:72px">HOME</a>
  <a style="width:82px">ABOUT US</a>
  <a style="width:80px">SERVICES</a>
  <a style="width:120px">NEWS AND EVENTS</a>
  <a style="width:64px">MEDIA</a>
  <a style="width:59px">BLOG</a>
  <a style="width:67px">FORUM</a>
  <a style="width:92px">CONTACT US</a>
  <a class="accent" style="width:74px">REGISTER</a>
  <a class="accent" style="width:67px;border-right:0">SIGNIN</a>
</nav>
<div class="abs subnav">
  <span style="left:18px">SUB MENU LINK</span>
  <span style="left:136px">SUB MENU LINK</span>
  <span style="left:253px">SUB MENU LINK</span>
  <span style="left:371px">SUB MENU LINK</span>
  <span style="left:488px">SUB MENU LINK</span>
</div>

<section class="abs slider">
  <div class="slide-photo" role="img" aria-label="Featured photo of a woman at a fashion event in front of a red sponsor backdrop"></div>
  <div class="caption">
    <h2>QUIS AUTEM VEL EUMIURE REPREHENDERIT</h2>
    <p>Sed rotiut perspiciatis unde omnis iste natus error porapa than it voluptatem accusantium doloremque laudantium, totam rem aperiam.</p>
    <a>November 17th, 2012</a>
  </div>
  <div class="prev"><svg width="10" height="14" viewBox="0 0 10 14"><path d="M9 0 L0 7 L9 14 Z" fill="#fff"/></svg></div>
</section>

<aside class="abs contact">
  <h3>CONTACT US</h3>
  <div class="field" style="top:53px">Name</div>
  <div class="field" style="top:86px">Phone</div>
  <div class="field" style="top:119px">E-mail</div>
  <div class="submit light" style="left:109px;top:155px;width:63px">SUBMIT</div>
</aside>

<section class="abs panel" style="top:419px;height:291px">
  <h2 style="top:14px">BLOG</h2>
  <div class="cards" style="top:37px">
    <article class="card">
      <div class="thumb"><div role="img" aria-label="Photo of officials saluting at a ceremony" style="background:linear-gradient(#6a7a5a,#3d3a3a)"></div></div>
      <h4>QUIS AUTEM VEL EUMIURE REPREHENDERIT</h4>
      <p>Sed rotiut perspiciatis unde omnis iste natus error porapa than it voluptatem accusantium doloremque laudantium, totam rem aperiam.</p>
      <div class="more">VIEW MORE</div>
    </article>
    <article class="card">
      <div class="thumb"><div role="img" aria-label="Photo of a man beside a silver sports car" style="background:linear-gradient(#8a8e90,#4a4c4e)"></div></div>
      <h4>QUIS AUTEM VEL EUMIURE REPREHENDERIT</h4>
      <p>Sed rotiut perspiciatis unde omnis iste natus error porapa than it voluptatem accusantium doloremque laudantium, totam rem aperiam.</p>
      <div class="more">VIEW MORE</div>
    </article>
    <article class="card">
      <div class="thumb"><div role="img" aria-label="Aerial photo of an airliner on a grassy airfield" style="background:linear-gradient(#7b9a5a,#4e6a3a)"></div></div>
      <h4>QUIS AUTEM VEL EUMIURE REPREHENDERIT</h4>
      <p>Sed rotiut perspiciatis unde omnis iste natus error porapa than it voluptatem accusantium doloremque laudantium, totam rem aperiam.</p>
      <div class="more">VIEW MORE</div>
    </article>
  </div>
</section>

<section class="abs panel" style="top:718px;height:228px">
  <h2 style="top:14px">UPCOMING EVENTS</h2>
  <div class="cards" style="top:40px">
    <article class="card">
      <div class="thumb"><div role="img" aria-label="Photo of photographers at a red carpet event" style="background:linear-gradient(#6a3a3a,#2e2a2a)"></div></div>
      <h4>QUIS AUTEM VEL EUMIURE REPREHENDERIT</h4>
      <div class="when">November 18th, 2012 &nbsp;&nbsp;at &nbsp;&nbsp;10.15am</div>
    </article>
    <article class="card">
      <div class="thumb"><div role="img" aria-label="Photo of a panel discussion on a stage" style="background:linear-gradient(#b84a4a,#3a3030)"></div></div>
      <h4>QUIS AUTEM VEL EUMIURE REPREHENDERIT</h4>
      <div class="when">November 18th, 2012 &nbsp;&nbsp;at &nbsp;&nbsp;10.15am</div>
    </article>
    <article class="card">
      <div class="thumb"><div role="img" aria-label="Photo of a photographer with a camera outdoors" style="background:linear-gradient(#4d7a3c,#2e3a2a)"></div></div>
      <h4>QUIS AUTEM VEL EUMIURE REPREHENDERIT</h4>
      <div class="when">November 18th, 2012 &nbsp;&nbsp;at &nbsp;&nbsp;10.15am</div>
    </article>
  </div>
</section>

<aside class="abs poll">
  <h3>OPENION POLL</h3>
  <p class="q">Sed rotiut perspiciatis unde than it voluptatem accusantium?</p>
  <ul>
    <li>Integer adipiscing</li>
    <li>Maecenas ac nunc</li>
    <li>Donec ut risus odio</li>
    <li>Vestibulum</li>
  </ul>
  <div class="submit">SUBMIT</div>
</aside>

<div class="abs ad" role="img" aria-label="Orange advertising banner for a film commission"></div>

<aside class="abs news">
  <h3>NEWSLETTER SUBSCRIBE</h3>
  <div class="field" style="left:10px;top:36px">Name</div>
  <div class="submit dark" style="left:111px;top:67px;width:63px">SUBMIT</div>
</aside>

<div class="abs tags">
  <span style="font-size:17px">delicious</span> <span class="s">display link item</span><br>
  <span style="font-size:11px">example</span> <span class="s">experience folder font</span><br>
  <span class="s">information interest</span> <span style="font-size:10px">items</span> <span class="s">keyword</span><br>
  <span style="font-size:14px">labels</span> <span style="font-size:14px">library</span> <span class="s">link</span> <span style="font-size:10px">online</span><br>
  <span class="s">organize person popular</span> <span style="font-size:12px">post</span> <span class="s">presidential</span><br>
  <span style="font-size:8px">public</span> <span class="s">recipe</span> <span style="font-size:7px">share site social speeches</span><br>
  <span class="s">subject</span> <span style="font-size:19px">tags</span> <span class="s">topic</span> <span style="font-size:11px">used</span> <span class="s">vocabulary</span><br>
  <span style="font-size:8px">web website wishlist words</span> <span class="s">youve</span>
</div>

<section>
  <div class="abs partners-title">PARTNERS</div>
  <div class="abs badge" style="left:94px;top:990px;width:100px;height:46px"></div>
  <div class="abs badge" style="left:232px;top:982px;width:124px;height:44px;background:#6b6b6b;border-radius:0"></div>
  <div class="abs badge" style="left:388px;top:988px;width:118px;height:34px"></div>
  <div class="abs badge" style="left:546px;top:990px;width:86px;height:30px"></div>
  <div class="abs badge" style="left:232px;top:1041px;width:84px;height:29px;background:#6b6b6b;border-radius:0"></div>
  <div class="abs badge" style="left:326px;top:1041px;width:30px;height:29px;background:#b0b0b0;border-radius:0"></div>
</section>

<footer class="abs footer">
  <div class="mark"></div>
  <div class="name">SteeringSpectrum</div>
  <div class="row" style="top:14px"><span>Home</span><span>About us</span><span>Services</span><span>News and Events</span><span>Media</span><span>Blog</span><span>Forum</span><span>Contact us</span><span>Register</span><span>Sign in</span></div>
  <div class="row plain" style="top:38px"><span>Copyright © 2012</span><span>www.steeringspectrum.com.au</span><span>All rights reserved.</span></div>
  <div class="row" style="top:62px"><span>Privacy Policy</span><span>Terms and conditions</span></div>
</footer>
</body>
</html>
```